Veltra Metrics New Website for Health Benefits Plan Decisioneering Tool Launch

Veltra Metrics is a SaaS provider of health benefits comparison tools. We need a new simple SaaS focused website to direct customers to our product

Target Market(s)

General Public comparing their health benefits plans from their employer or from the state exchanges in the US

Coding

Coded - Design and coding required

Number of Pages Required

3 page

Requirements
Must have
• Main page - "Know the Best Health Benefits Plan for You!"
Graphic of a person looking over papers on their desk
Compare Now button to link to SaaS product
About Us
Product Page

https://plimbo.example/top-app-pages/

```html
<!DOCTYPE html>
<html lang="en">
<head>
<meta charset="utf-8">
<title>Veltra Metrics — Know the Best Health Benefits Plan for You</title>
<link rel="stylesheet" href="https://fonts.googleapis.com/css2?family=Cinzel:wght@400;700&family=Quicksand:wght@500;600;700&display=swap">
<style>
  :root {
    --brand-blue: #29a9e1;
    --pale-blue: #dbeffa;
    --white: #ffffff;
    --frame-grey: #666666;
    --text-dark: #333333;
    --scene-light: #e9eef2;
    --scene-mid: #c9d3db;
  }
  * { margin: 0; padding: 0; box-sizing: border-box; }
  html, body { width: 1200px; height: 727px; overflow: hidden; }
  body {
    position: relative;
    background: var(--pale-blue);
    font-family: "Quicksand", sans-serif;
    color: var(--white);
  }
  .backdrop { position: absolute; inset: 0; }
  .site-header { position: absolute; inset: 0 0 auto 0; height: 90px; }
  .brand {
    position: absolute; left: 141px; top: 30px;
    font-family: "Cinzel", serif; font-weight: 400;
    font-size: 31px; letter-spacing: 0.5px; color: var(--white);
    text-decoration: none; white-space: nowrap;
  }
  .main-nav { position: absolute; top: 34px; left: 557px; display: flex; gap: 31px; }
  .main-nav a {
    color: var(--white); text-decoration: none;
    font-weight: 700; font-size: 13px; letter-spacing: 0.4px;
  }
  .contact-button {
    position: absolute; left: 880px; top: 24px; width: 135px; height: 39px;
    background: var(--brand-blue); color: var(--white); border-radius: 3px;
    display: flex; align-items: center; justify-content: center;
    font-weight: 700; font-size: 13px; letter-spacing: 0.4px; text-decoration: none;
  }
  .hero-copy { position: absolute; left: 142px; top: 222px; }
  .hero-title {
    font-family: "Cinzel", serif; font-weight: 400;
    font-size: 43px; line-height: 51px; letter-spacing: 0.6px; color: var(--white);
  }
  .compare-button {
    display: inline-flex; align-items: center; justify-content: center;
    margin-top: 26px; width: 148px; height: 39px;
    background: var(--white); color: var(--brand-blue); border-radius: 3px;
    font-weight: 600; font-size: 13px; letter-spacing: 0.4px; text-decoration: none;
  }
  .hero-illustration { position: absolute; left: 577px; top: 80px; width: 508px; height: 508px; }
  .site-footer {
    position: absolute; left: 0; right: 0; top: 655px; height: 42px;
    display: flex; align-items: center; justify-content: space-between;
    padding: 0 142px 0 143px; color: var(--text-dark);
  }
  .copyright { font-size: 12.5px; font-weight: 500; }
  .copyright .company { font-family: "Cinzel", serif; font-size: 13px; }
  .social-links { display: flex; gap: 9px; }
  .social-links a {
    width: 35px; height: 35px; border-radius: 50%;
    background: var(--brand-blue); display: block;
  }
</style>
</head>
<body>
  <svg class="backdrop" width="1200" height="727" viewBox="0 0 1200 727" aria-hidden="true">
    <path d="M0 0 H830 V590 C700 612 480 638 367 632 C250 626 110 600 0 557 Z" fill="var(--brand-blue)"/>
    <path d="M0 633 C300 614 680 590 880 587 C1030 586 1140 608 1200 640 V727 H0 Z" fill="var(--white)"/>
  </svg>

  <header class="site-header">
    <a class="brand" href="#">Veltra Metrics</a>
    <nav class="main-nav">
      <a href="#">HOME</a>
      <a href="#">ABOUT US</a>
      <a href="#">PRODUCT</a>
    </nav>
    <a class="contact-button" href="#">CONTACT US</a>
  </header>

  <section class="hero-copy">
    <h1 class="hero-title">KNOW THE BEST<br>HEALTH BENEFITS<br>PLAN FOR YOU!</h1>
    <a class="compare-button" href="https://plimbo.example/top-app-pages/">COMPARE NOW</a>
  </section>

  <svg class="hero-illustration" viewBox="0 0 508 508" role="img" aria-label="Illustration of an office where a person looks over papers at a desk with an advisor, shelves of binders behind them">
    <defs>
      <linearGradient id="sceneTone" x1="0" y1="0" x2="0" y2="1">
        <stop offset="0" stop-color="var(--scene-mid)"/>
        <stop offset="1" stop-color="var(--scene-light)"/>
      </linearGradient>
    </defs>
    <circle cx="254" cy="254" r="250" fill="url(#sceneTone)" stroke="var(--frame-grey)" stroke-width="8"/>
  </svg>

  <footer class="site-footer">
    <p class="copyright">Copyright © 2020 <span class="company">VELTRA METRICS LLC.</span> All Rights Reserved.</p>
    <nav class="social-links" aria-label="Social media">
      <a href="#" aria-label="Social profile 1"></a>
      <a href="#" aria-label="Social profile 2"></a>
      <a href="#" aria-label="Social profile 3"></a>
      <a href="#" aria-label="Social profile 4"></a>
    </nav>
  </footer>
</body>
</html>
```